Fresh, modern, fun business card for pediatric dental practice

Need a business card for fresh, modern, fun pediatric dental practice

Clean look that matches our website's font and colors

We prefer the look of curved corners on business cards

Target Market(s)

parents (mothers) of young children, professionals, mid-high class

Industry/Entity Type

Dental

Contact Information for Business Card

Maplebrook Pediatric Dentistry
482 Quarry Lane
Suite 517
Alderwick, ST 00123
717.555.0193
www.maplebrookkidsdental.example

Mei-Ran Tsai, DMD
Corinne Walbeck, DMD
(we are working on our email address, but we would like that on the card as well)

Font styles to use
Sans Serif

Requirements
Must have
• All info; we would also like to make cards for individual staff members
• colors from our website and color palatte, attatched
• use same font and design as website for branding
Nice to have
• clean, simple card that has a pop of color
• we would like to see a few designs with our tag line "where smiles get brighter"
• we are not sure if we want to have it on there or not
• we would like to see a few designs incorporating the ribbon graphic on our website where the word WELCOME is

```html
<!DOCTYPE html>
<html lang="en">
<head>
<meta charset="utf-8">
<title>Maplebrook Pediatric Dentistry – Business Card</title>
<link href="https://fonts.googleapis.com/css2?family=Open+Sans:wght@400;600;700&display=swap" rel="stylesheet">
<style>
  :root {
    --page: #e9e6e1;
    --card-black: #141214;
    --sun-yellow: #f6b824;
    --berry-pink: #d4318f;
    --paper-white: #f4f2ef;
    --ink-dark: #1c1a1b;
  }
  * { margin: 0; padding: 0; box-sizing: border-box; }
  html, body {
    width: 1200px; height: 900px; overflow: hidden;
    background: var(--page);
    font-family: "Open Sans", sans-serif;
  }
  .canvas { position: relative; width: 1200px; height: 900px; }

  .card {
    position: absolute;
    width: 560px; height: 320px;
    background: var(--card-black);
    border-radius: 18px;
    overflow: hidden;
    box-shadow: 0 10px 28px rgba(0,0,0,0.22);
  }
  .card-front { left: 140px; top: 120px; }
  .card-back  { left: 500px; top: 440px; }

  /* Front: practice name */
  .brand {
    position: absolute; left: 0; right: 0; top: 108px;
    display: flex; align-items: center; justify-content: center; gap: 16px;
    color: var(--sun-yellow); font-weight: 600;
  }
  .brand-mark {
    width: 44px; height: 44px; border-radius: 50%;
    border: 4px solid var(--sun-yellow); flex: none;
  }
  .brand-name { line-height: 1.05; }
  .brand-name .primary { display: block; font-size: 50px; letter-spacing: 0.5px; }
  .brand-name .secondary { display: block; font-size: 22px; letter-spacing: 2px; }

  /* Back: contact details */
  .doctors {
    position: absolute; left: 48px; top: 30px;
    color: var(--berry-pink); font-weight: 700; font-size: 20px; line-height: 25px;
  }
  .contact-list {
    position: absolute; left: 48px; top: 92px; list-style: none;
    color: var(--paper-white); font-size: 15px; line-height: 20px;
  }
  .contact-list li { display: flex; align-items: center; gap: 8px; }
  .contact-list svg { width: 12px; height: 12px; flex: none; fill: var(--berry-pink); }
  .address {
    position: absolute; left: 48px; top: 176px;
    color: var(--paper-white); font-size: 15px; line-height: 19px; font-style: normal;
  }
  .wave { position: absolute; left: 0; top: 0; width: 560px; height: 320px; }
  .wave-url {
    position: absolute; right: 26px; top: 262px;
    color: var(--ink-dark); font-size: 14px; font-weight: 600;
  }
</style>
</head>
<body>
<main class="canvas">

  <section class="card card-front" aria-label="Card front">
    <div class="brand">
      <span class="brand-mark" aria-hidden="true"></span>
      <span class="brand-name">
        <span class="primary">maplebrook</span>
        <span class="secondary">pediatric dentistry</span>
      </span>
    </div>
  </section>

  <section class="card card-back" aria-label="Card back">
    <svg class="wave" viewBox="0 0 560 320" aria-hidden="true">
      <path d="M0 272 C 200 268, 380 210, 560 130 L560 320 L0 320 Z" fill="var(--sun-yellow)"/>
      <path d="M0 250 C 180 252, 330 222, 430 178 C 340 230, 180 265, 0 265 Z" fill="var(--berry-pink)"/>
    </svg>

    <div class="doctors">
      <div>Mei-Ran Tsai, DMD</div>
      <div>Corinne Walbeck, DMD</div>
    </div>

    <ul class="contact-list">
      <li>
        <svg viewBox="0 0 12 12" aria-hidden="true"><path d="M2 1h2.5l1 3-1.5 1a6 6 0 0 0 3 3l1-1.5 3 1V10a1 1 0 0 1-1 1A9 9 0 0 1 1 2a1 1 0 0 1 1-1z"/></svg>
        555.555.0193
      </li>
      <li>
        <svg viewBox="0 0 12 12" aria-hidden="true"><path d="M1 2.5h10v7H1z"/><path d="M1.5 3l4.5 3.5L10.5 3" fill="none" stroke="#141214" stroke-width="1"/></svg>
        Mei-ran@maplebrookkidsdental.example
      </li>
      <li>
        <svg viewBox="0 0 12 12" aria-hidden="true"><path d="M1 2.5h10v7H1z"/><path d="M1.5 3l4.5 3.5L10.5 3" fill="none" stroke="#141214" stroke-width="1"/></svg>
        Corinne@maplebrookkidsdental.example
      </li>
      <li>
        <svg viewBox="0 0 12 12" aria-hidden="true"><path d="M4.5 7.5l3-3" stroke="var(--berry-pink)" stroke-width="1.4"/><circle cx="3.5" cy="8.5" r="2.2" fill="none" stroke="var(--berry-pink)" stroke-width="1.4"/><circle cx="8.5" cy="3.5" r="2.2" fill="none" stroke="var(--berry-pink)" stroke-width="1.4"/></svg>
        www.maplebrookkidsdental.example
      </li>
    </ul>

    <address class="address">
      Maplebrook Pediatric Dentistry<br>
      482 Quarry Lane Suite 517<br>
      Alderwick, ST 00123
    </address>

    <div class="wave-url">www.maplebrookkidsdental.example</div>
  </section>

</main>
</body>
</html>
```